Business card design for Automotive workshop

We need a business card for a new automotive repair and tyre shop called Keelstone Prime Automotive located in New Zealand. We are a clean, modern and fresh workshop and company.

Front needs to feature logo,
my name:
Marlo Fenwicke (director)

Address:
48 Tarn Lane
Harrowby 3847

Phone: 07 594 2713
Mobile: 027 451 9362
Email: office@keelstoneautomotive.example.nz
Website: keelstoneautomotive.example.nz

Back needs to feature an area to write down appointment details, date and time.

Also feature a list of jobs and work we do such as,
Vehicle Servicing
All Mechanical Repairs
Warrant of Fitness
Tyres & Wheel Alignments
Automotive Diagnostics
Automotive Parts & Supplies

```html
<!DOCTYPE html>
<html lang="en">
<head>
<meta charset="utf-8">
<title>Keelstone Prime Automotive – Business Card</title>
<link href="https://fonts.googleapis.com/css2?family=Roboto:ital,wght@0,300;0,400;0,500;0,700;1,400&display=swap" rel="stylesheet">
<style>
  :root {
    --backdrop: #3b3532;
    --card: #2b2b2d;
    --red: #e3202a;
    --white: #f2f2f2;
    --muted: #d6d6d6;
    --emboss: #1e1e20;
    --rule: #cfcfcf;
  }
  * { margin: 0; padding: 0; box-sizing: border-box; }
  html, body {
    width: 1200px; height: 847px; overflow: hidden;
    background: var(--backdrop);
    font-family: "Roboto", Arial, sans-serif;
    color: var(--white);
  }
  .canvas { position: relative; width: 1200px; height: 847px; }

  .card {
    position: absolute;
    width: 540px; height: 310px;
    background: var(--card);
    border-bottom: 5px solid var(--red);
    box-shadow: 0 10px 24px rgba(0,0,0,.35);
  }
  .card--back { left: 50px; top: 120px; }
  .card--front { left: 610px; top: 400px; }

  /* Back: appointment */
  .wordmark-faint {
    position: absolute; left: 150px; top: 28px; width: 340px;
    text-align: center;
    font-weight: 700; font-size: 30px; letter-spacing: 1px; line-height: 1.05;
    color: var(--emboss); text-transform: uppercase;
  }
  .appt-title {
    position: absolute; left: 0; right: 0; top: 108px; text-align: center;
    color: var(--red); font-size: 15px; font-style: italic; letter-spacing: .5px;
  }
  .field { position: absolute; top: 140px; display: flex; align-items: flex-end; font-size: 13px; font-style: italic; }
  .field .line { border-bottom: 1px solid var(--rule); height: 1px; margin-left: 6px; margin-bottom: 3px; }
  .field--date { left: 30px; }
  .field--date .line { width: 200px; }
  .field--time { left: 290px; }
  .field--time .line { width: 180px; }
  .days {
    position: absolute; left: 30px; right: 40px; top: 182px;
    display: flex; justify-content: space-between; list-style: none;
    font-size: 13px; font-style: italic;
  }
  .days li { display: flex; align-items: center; gap: 6px; }
  .days .box { width: 11px; height: 11px; border: 1px solid var(--red); border-radius: 50%; }
  .services {
    position: absolute; left: 20px; right: 20px; bottom: 26px;
    text-align: center; font-size: 12.5px; font-style: italic; line-height: 1.7; color: var(--muted);
  }
  .services .dot { color: var(--red); margin: 0 4px; }

  /* Front */
  .wordmark {
    position: absolute; right: 32px; top: 34px; width: 330px; text-align: center;
    font-weight: 700; font-size: 30px; line-height: 1.05; letter-spacing: 1px;
    color: var(--red); text-transform: uppercase;
  }
  .identity { position: absolute; left: 30px; top: 168px; width: 212px; }
  .identity .name { color: var(--red); font-weight: 500; font-size: 20px; text-transform: uppercase; white-space: nowrap; }
  .identity .role { text-align: right; font-size: 15px; margin-top: 2px; }
  .identity .address { font-size: 14px; margin-top: 10px; color: var(--muted); }
  .divider { position: absolute; left: 256px; top: 176px; width: 1px; height: 82px; background: var(--red); }
  .contacts { position: absolute; left: 268px; top: 174px; list-style: none; font-size: 12.5px; line-height: 1.65; }
  .contacts li { display: flex; align-items: center; gap: 6px; white-space: nowrap; }
  .contacts svg { width: 12px; height: 12px; fill: var(--red); flex: none; }
</style>
</head>
<body>
<main class="canvas">

  <section class="card card--back" aria-label="Card back: appointment">
    <div class="wordmark-faint">Keelstone Prime<br>Automotive</div>
    <div class="appt-title">APPOINTMENT</div>
    <div class="field field--date">Date:<span class="line"></span></div>
    <div class="field field--time">Time:<span class="line"></span></div>
    <ul class="days">
      <li><span class="box"></span>Mon</li>
      <li><span class="box"></span>Tue</li>
      <li><span class="box"></span>Wed</li>
      <li><span class="box"></span>Thu</li>
      <li><span class="box"></span>Fri</li>
    </ul>
    <p class="services">
      Vehicle Servicing<span class="dot">•</span>All Mechanical Repairs<span class="dot">•</span>Warrant of Fitness<br>
      Tyres &amp; Wheel Alignments<span class="dot">•</span>Automotive Diagnostics<span class="dot">•</span>Automotive Parts &amp; Supplies
    </p>
  </section>

  <section class="card card--front" aria-label="Card front: contact details">
    <div class="wordmark">Keelstone Prime<br>Automotive</div>
    <div class="identity">
      <div class="name">Marlo Fenwicke</div>
      <div class="role">director</div>
      <div class="address">48 Tarn Lane, Harrowby 3847</div>
    </div>
    <div class="divider"></div>
    <ul class="contacts">
      <li><svg viewBox="0 0 24 24"><path d="M6.6 10.8a15 15 0 0 0 6.6 6.6l2.2-2.2a1 1 0 0 1 1-.25 11.4 11.4 0 0 0 3.6.57 1 1 0 0 1 1 1V20a1 1 0 0 1-1 1A17 17 0 0 1 3 4a1 1 0 0 1 1-1h3.5a1 1 0 0 1 1 1c0 1.25.2 2.45.57 3.570a1 1 0 0 1-.25 1z"/></svg>07 594 2713</li>
      <li><svg viewBox="0 0 24 24"><path d="M7 1h10a2 2 0 0 1 2 2v18a2 2 0 0 1-2 2H7a2 2 0 0 1-2-2V3a2 2 0 0 1 2-2zm0 3v14h10V4zm5 15.5a1 1 0 1 0 0 2 1 1 0 0 0 0-2z"/></svg>027 451 9362</li>
      <li><svg viewBox="0 0 24 24"><path d="M2 5h20v14H2zm2 2v.5l8 5 8-5V7l-8 5z"/></svg>office@keelstoneautomotive.example.nz</li>
      <li><svg viewBox="0 0 24 24"><path d="M12 2a10 10 0 1 0 0 20 10 10 0 0 0 0-20zm6.9 9h-3a15 15 0 0 0-1.3-5.6A8 8 0 0 1 18.9 11zM12 4c.9 1.3 1.7 3.6 1.9 7h-3.8C10.3 7.6 11.1 5.3 12 4zM9.4 5.4A15 15 0 0 0 8.1 11h-3a8 8 0 0 1 4.3-5.6zM5.1 13h3a15 15 0 0 0 1.3 5.6A8 8 0 0 1 5.1 13zM12 20c-.9-1.3-1.7-3.6-1.9-7h3.8c-.2 3.4-1 5.7-1.9 7zm2.6-1.4a15 15 0 0 0 1.3-5.6h3a8 8 0 0 1-4.3 5.6z"/></svg>keelstoneautomotive.example.nz</li>
    </ul>
  </section>

</main>
</body>
</html>
```